Corporate Dinner Invite at Corvessa for BRQ

BRQ is hosting a corporate dinner at the VEP Summit and we need an email attachment invite for the event. Please use some images from this site for inspiration: https://www.corvessadining.example/ivyparlor/

Invite Title:
Join us for dinner!

Event Details:
Tuesday, October 24th 2023 at 6:30pm
Corvessa Dining, Ivy Parlor
347 W Marlow Ave, Chicago, IL 60622

Target Market(s)

Corporate Audience

Font styles to use
Script

Colors
0054AA
0677BA
7BADD7
CADEEF
E8F1F8

Requirements
Must have
• BRQ logo, event date / time, event location details, photo(s) from Ivy Parlor

```html
<!DOCTYPE html>
<html lang="en">
<head>
<meta charset="UTF-8">
<title>BRQ Dinner Invitation – VEP Summit</title>
<link rel="stylesheet" href="https://fonts.googleapis.com/css2?family=Kaushan+Script&family=Dancing+Script:wght@600;700&family=Poppins:wght@500;700&display=swap">
<style>
  :root {
    --blue-deep: #0054AA;
    --blue-mid: #0677BA;
    --blue-soft: #7BADD7;
    --blue-pale: #CADEEF;
    --blue-mist: #E8F1F8;
    --navy-ink: #16328a;
    --accent-orange: #F0962A;
    --paper: #ffffff;
  }
  html, body {
    margin: 0;
    padding: 0;
    overflow: hidden;
    background: var(--paper);
  }
  .invite {
    position: relative;
    width: 900px;
    height: 1200px;
    overflow: hidden;
    background: var(--paper);
  }
  .side-bands {
    position: absolute;
    inset: 0;
  }
  .brand {
    position: absolute;
    top: 105px;
    left: 0;
    width: 900px;
    display: flex;
    justify-content: center;
    align-items: center;
    gap: 16px;
  }
  .brand-mark {
    width: 54px;
    height: 54px;
    background: var(--blue-deep);
  }
  .brand-name {
    font-family: "Poppins", sans-serif;
    font-weight: 700;
    font-size: 62px;
    letter-spacing: 4px;
    color: var(--blue-deep);
    line-height: 1;
  }
  .title {
    position: absolute;
    left: 0;
    width: 900px;
    text-align: center;
    font-family: "Kaushan Script", cursive;
    color: var(--accent-orange);
    margin: 0;
    font-weight: 400;
  }
  .title-lead {
    top: 200px;
    font-size: 66px;
    line-height: 1;
  }
  .title-main {
    top: 265px;
    font-size: 128px;
    line-height: 1;
  }
  .photo {
    position: absolute;
    border: 6px solid var(--paper);
    box-shadow: 0 6px 16px rgba(0, 0, 0, 0.25);
  }
  .photo-bar {
    left: 100px;
    top: 450px;
    width: 225px;
    height: 150px;
    transform: rotate(-4deg);
    background: linear-gradient(135deg, #2a1d12, #6b4a2b 55%, #c9a27a);
  }
  .photo-lounge {
    left: 300px;
    top: 430px;
    width: 255px;
    height: 175px;
    transform: rotate(3deg);
    background: linear-gradient(160deg, #3a2614, #8a5d33 50%, #2b1a0e);
    z-index: 2;
  }
  .photo-room {
    left: 500px;
    top: 455px;
    width: 310px;
    height: 170px;
    transform: rotate(-5deg);
    background: linear-gradient(120deg, #1c120a, #7a4f2a 45%, #d7a46a 70%, #2a1a0d);
    z-index: 3;
  }
  .venue-line {
    position: absolute;
    top: 700px;
    left: 300px;
    margin: 0;
    font-family: "Poppins", sans-serif;
    font-weight: 500;
    font-size: 40px;
    color: var(--blue-mid);
  }
  .details {
    position: absolute;
    top: 765px;
    left: 200px;
    margin: 0;
    padding: 0;
    list-style: none;
    font-family: "Dancing Script", cursive;
    font-weight: 700;
    color: var(--navy-ink);
  }
  .detail {
    display: flex;
    align-items: flex-start;
    gap: 18px;
    margin-bottom: 12px;
    font-size: 40px;
    line-height: 1.05;
  }
  .detail-icon {
    flex: none;
    width: 32px;
    height: 32px;
    margin-top: 8px;
  }
  .detail-address {
    font-size: 38px;
  }
  .sign-off {
    position: absolute;
    top: 1005px;
    left: 0;
    width: 900px;
    margin: 0;
    text-align: center;
    font-family: "Dancing Script", cursive;
    font-weight: 700;
    font-size: 74px;
    color: var(--navy-ink);
  }
</style>
</head>
<body>
<main class="invite">
  <svg class="side-bands" width="900" height="1200" viewBox="0 0 900 1200" aria-hidden="true">
    <defs>
      <linearGradient id="band-left" x1="0" y1="0" x2="1" y2="0">
        <stop offset="0" stop-color="#0a2f8a"/>
        <stop offset="1" stop-color="#0054AA"/>
      </linearGradient>
      <linearGradient id="band-right" x1="1" y1="0" x2="0" y2="0">
        <stop offset="0" stop-color="#0a2f8a"/>
        <stop offset="1" stop-color="#0054AA"/>
      </linearGradient>
    </defs>
    <path d="M0 0 H150 C60 200 40 500 50 700 C60 900 130 1080 220 1200 H0 Z" fill="#CADEEF"/>
    <path d="M0 0 H120 C40 220 25 500 35 700 C45 900 100 1080 180 1200 H0 Z" fill="#7BADD7"/>
    <path d="M0 0 H100 C25 230 10 500 20 700 C30 900 80 1080 150 1200 H0 Z" fill="url(#band-left)"/>
    <path d="M900 0 H750 C840 200 860 500 850 700 C840 900 770 1080 680 1200 H900 Z" fill="#CADEEF"/>
    <path d="M900 0 H780 C860 220 875 500 865 700 C855 900 800 1080 720 1200 H900 Z" fill="#7BADD7"/>
    <path d="M900 0 H800 C875 230 890 500 880 700 C870 900 820 1080 750 1200 H900 Z" fill="url(#band-right)"/>
  </svg>

  <header class="brand">
    <span class="brand-mark"></span>
    <span class="brand-name">BRQ</span>
  </header>

  <h1 class="title title-lead">Join us for</h1>
  <p class="title title-main">Dinner!</p>

  <div class="photo photo-bar" role="img" aria-label="Cocktails on the bar counter at Ivy Parlor"></div>
  <div class="photo photo-lounge" role="img" aria-label="Warmly lit lounge seating at Ivy Parlor"></div>
  <div class="photo photo-room" role="img" aria-label="Ivy Parlor dining room with bar and chandeliers"></div>

  <p class="venue-line">@ VEP Summit</p>

  <ul class="details">
    <li class="detail">
      <svg class="detail-icon" viewBox="0 0 24 24" aria-hidden="true">
        <rect x="2" y="4" width="20" height="18" rx="2" fill="#0677BA"/>
        <rect x="2" y="4" width="20" height="5" fill="#0054AA"/>
        <rect x="6" y="1" width="2.5" height="5" fill="#0054AA"/>
        <rect x="15.5" y="1" width="2.5" height="5" fill="#0054AA"/>
        <g fill="#ffffff"><rect x="5" y="11" width="3" height="3"/><rect x="10.5" y="11" width="3" height="3"/><rect x="16" y="11" width="3" height="3"/><rect x="5" y="16" width="3" height="3"/><rect x="10.5" y="16" width="3" height="3"/></g>
      </svg>
      <span>Tuesday, October 24th, 2023</span>
    </li>
    <li class="detail">
      <svg class="detail-icon" viewBox="0 0 24 24" aria-hidden="true">
        <circle cx="12" cy="12" r="10" fill="none" stroke="#0677BA" stroke-width="2.5"/>
        <path d="M12 6 V12 L16 14.5" fill="none" stroke="#0677BA" stroke-width="2.5" stroke-linecap="round"/>
      </svg>
      <span>6:30pm</span>
    </li>
    <li class="detail detail-address">
      <svg class="detail-icon" viewBox="0 0 24 24" aria-hidden="true">
        <circle cx="12" cy="12" r="10.5" fill="none" stroke="#0677BA" stroke-width="2"/>
        <path d="M12 4.5 C8.8 4.5 7 6.8 7 9.3 C7 12.8 12 18.5 12 18.5 C12 18.5 17 12.8 17 9.3 C17 6.8 15.2 4.5 12 4.5 Z" fill="#0677BA"/>
        <circle cx="12" cy="9.4" r="2" fill="#ffffff"/>
      </svg>
      <span>Corvessa Dining, Ivy Parlor<br>347 W Marlow Ave, Chicago, IL 60622</span>
    </li>
  </ul>

  <p class="sign-off">See You There!</p>
</main>
</body>
</html>
```